Spring Detox sale graphics for social media

You MUST read the Brief in the WORD document and follow the instructions there. I want to create 10 social media graphics (new Instagram size 4:5 (1080 x 1350 pixels) focusing on our Mother’s Day Spring Detox Sale graphics, using any of the pics attached. Use the attached pics, NO RANDOM STOCK PHOTOGRAPHY. For the color scheme of the graphics, they should all be complementary to the product colors or feel like Spring time.

Target Market(s)

primarily women

Requirements
Must have
• the photos and text attached

```html
<!DOCTYPE html>
<html lang="en">
<head>
<meta charset="utf-8">
<title>Mother's Day Spring Detox Sale</title>
<link rel="stylesheet" href="https://fonts.googleapis.com/css2?family=Montserrat:wght@400;500;700;800&family=Playfair+Display:wght@400;500&family=Great+Vibes&display=swap">
<style>
  :root {
    --pink: #e0245e;
    --pink-ring: #f3a9b8;
    --blush: #fbe6ea;
    --green-dark: #3b5a1c;
    --text-dark: #3d3a3a;
    --white: #ffffff;
    --marble: #ece8e4;
  }
  * { margin: 0; padding: 0; box-sizing: border-box; }
  html, body { width: 910px; height: 1200px; overflow: hidden; }
  body { background: var(--blush); }
  .poster {
    position: relative;
    width: 910px;
    height: 1200px;
    overflow: hidden;
    font-family: "Montserrat", sans-serif;
  }
  .backdrop {
    position: absolute; inset: 0;
    background:
      radial-gradient(ellipse at 50% 28%, #fdf1f3 0%, rgba(253,241,243,0.9) 35%, rgba(253,241,243,0) 70%),
      linear-gradient(180deg, #fbe4ea 0%, #f6e4e6 40%, #e4ecd0 75%, #f4d9e0 100%);
  }
  .counter {
    position: absolute; left: 0; right: 0; top: 1108px; bottom: 0;
    background: linear-gradient(180deg, #f1ede9, var(--marble));
  }
  .headline { position: absolute; left: 0; right: 0; text-align: center; white-space: nowrap; }
  .discount {
    top: 56px;
    color: var(--pink);
    font-weight: 800;
    line-height: 1;
    letter-spacing: -2px;
  }
  .discount .pct { font-size: 128px; }
  .discount .off { font-size: 94px; letter-spacing: 1px; margin-left: 14px; }
  .occasion {
    top: 198px;
    font-family: "Playfair Display", serif;
    font-weight: 400;
    font-size: 86px;
    color: var(--pink);
    line-height: 1;
    letter-spacing: 7px;
  }
  .sale-title {
    top: 292px;
    font-family: "Great Vibes", cursive;
    font-size: 104px;
    color: var(--green-dark);
    line-height: 1;
  }
  .divider { position: absolute; left: 230px; top: 398px; }
  .benefits { position: absolute; left: 84px; top: 484px; list-style: none; }
  .benefit { display: flex; align-items: center; height: 107px; }
  .benefit-icon {
    width: 90px; height: 90px; border-radius: 50%;
    border: 2px solid var(--pink-ring);
    background: rgba(253,232,236,0.85);
    display: flex; align-items: center; justify-content: center;
    flex-shrink: 0;
  }
  .benefit-text { margin-left: 16px; }
  .benefit-title {
    font-size: 18px; font-weight: 700; color: var(--green-dark);
    letter-spacing: 0.3px;
  }
  .benefit-desc {
    font-size: 15.5px; font-weight: 400; color: var(--text-dark);
    line-height: 1.45; margin-top: 4px;
  }
  .person-photo {
    position: absolute; left: 442px; top: 452px; width: 342px; height: 520px;
    background: linear-gradient(180deg, #f2d9d0 0%, #efe9e8 45%, #e9e3e4 75%, #f4f1f2 100%);
    border-radius: 4px;
  }
  .product-photo {
    position: absolute; left: 308px; top: 960px; width: 522px; height: 196px;
    background: linear-gradient(180deg, #fbfafa 0%, #f1eeee 60%, #e7e2e4 100%);
    border-radius: 4px;
  }
  .badge {
    position: absolute; left: 68px; top: 907px; width: 228px; height: 228px;
    border-radius: 50%;
    border: 4px solid var(--white);
    background: radial-gradient(circle at 50% 40%, #f9c3cf 0%, #f39bb0 60%, #ec8ba2 100%);
    text-align: center; color: var(--white);
    display: flex; flex-direction: column; align-items: center; justify-content: center;
  }
  .badge-words {
    font-weight: 700; font-size: 29px; line-height: 1.06; letter-spacing: 1.5px;
    margin-top: 6px;
  }
  .badge-tag {
    font-family: "Great Vibes", cursive; font-size: 31px; color: var(--green-dark);
    margin-top: 4px;
  }
</style>
</head>
<body>
<main class="poster">
  <div class="backdrop" role="img" aria-label="Soft spring backdrop of pink blossoms and green foliage"></div>
  <div class="counter"></div>

  <h1 class="headline discount"><span class="pct">25%</span><span class="off">OFF</span></h1>
  <h2 class="headline occasion">MOTHER’S DAY</h2>
  <h2 class="headline sale-title">Spring Detox Sale</h2>

  <svg class="divider" width="450" height="50" viewBox="0 0 450 50" aria-hidden="true">
    <line x1="0" y1="27" x2="183" y2="27" stroke="#e0245e" stroke-width="2"/>
    <line x1="262" y1="27" x2="431" y2="27" stroke="#e0245e" stroke-width="2"/>
    <path d="M222 44 C207 32 199 25 199 16 C199 9 205 4 211 4 C216 4 220 7 222 11 C224 7 228 4 233 4 C239 4 245 9 245 16 C245 25 237 32 222 44 Z" fill="#e0245e"/>
  </svg>

  <ul class="benefits">
    <li class="benefit">
      <div class="benefit-icon">
        <svg width="50" height="50" viewBox="0 0 50 50" fill="none" stroke="#3b5a1c" stroke-width="2" aria-hidden="true">
          <path d="M8 42 C8 20 22 8 44 6 C44 28 32 42 12 40 Z"/>
          <path d="M8 42 L34 16"/>
        </svg>
      </div>
      <div class="benefit-text">
        <div class="benefit-title">DETOX &amp; CLEANSE</div>
        <div class="benefit-desc">Support your body<br>naturally*</div>
      </div>
    </li>
    <li class="benefit">
      <div class="benefit-icon">
        <svg width="56" height="50" viewBox="0 0 56 50" fill="none" stroke="#3b5a1c" stroke-width="2" aria-hidden="true">
          <path d="M28 6 V44 M18 44 H38 M8 12 H48"/>
          <circle cx="28" cy="8" r="2.5"/>
          <path d="M12 12 L4 28 H20 Z M44 12 L36 28 H52 Z"/>
          <path d="M4 28 C6 34 18 34 20 28 M36 28 C38 34 50 34 52 28"/>
        </svg>
      </div>
      <div class="benefit-text">
        <div class="benefit-title">HORMONE BALANCE</div>
        <div class="benefit-desc">Promote healthy<br>hormone levels*</div>
      </div>
    </li>
    <li class="benefit">
      <div class="benefit-icon">
        <svg width="50" height="56" viewBox="0 0 50 56" fill="none" stroke="#3b5a1c" stroke-width="2" aria-hidden="true">
          <path d="M12 4 C16 14 14 22 8 30 C4 38 6 46 10 52"/>
          <path d="M38 4 C34 14 36 22 42 30 C46 38 44 46 40 52"/>
          <circle cx="25" cy="28" r="1.5"/>
          <path d="M8 38 C18 40 32 40 42 38 M12 42 C18 48 32 48 38 42"/>
        </svg>
      </div>
      <div class="benefit-text">
        <div class="benefit-title">DIGESTIVE SUPPORT</div>
        <div class="benefit-desc">Aid digestion and<br>reduce bloating*</div>
      </div>
    </li>
    <li class="benefit">
      <div class="benefit-icon">
        <svg width="48" height="54" viewBox="0 0 48 54" fill="none" stroke="#3b5a1c" stroke-width="2" aria-hidden="true">
          <path d="M24 4 L42 10 V26 C42 38 34 46 24 50 C14 46 6 38 6 26 V10 Z"/>
          <path d="M20 18 H28 V24 H34 V32 H28 V38 H20 V32 H14 V24 H20 Z"/>
        </svg>
      </div>
      <div class="benefit-text">
        <div class="benefit-title">OVERALL WELLNESS</div>
        <div class="benefit-desc">Feel refreshed, energized<br>&amp; renewed*</div>
      </div>
    </li>
  </ul>

  <div class="person-photo" role="img" aria-label="Smiling woman in a white cropped sweater pointing down toward the products"></div>
  <div class="product-photo" role="img" aria-label="Row of wellness supplement bottles and cream tubes on a marble counter"></div>

  <div class="badge">
    <svg width="36" height="32" viewBox="0 0 36 32" fill="none" stroke="#ffffff" stroke-width="2" aria-hidden="true">
      <path d="M18 29 C6 20 2 15 2 9 C2 5 5 2 9 2 C13 2 16 4 18 8 C20 4 23 2 27 2 C31 2 34 5 34 9 C34 15 30 20 18 29 Z"/>
    </svg>
    <div class="badge-words">DETOX.<br>RESET.<br>GLOW.</div>
    <div class="badge-tag">You deserve it!</div>
  </div>
</main>
</body>
</html>
```